Business Card & Email Signature Design || Upmarket + Luxury

Rima Vale Honey, a New Zealand Manuka Honey company needs a Business Card & Email Signature design.

Our logo's are attached in Gold & Black versions, feel free to be creative with how you use the logo and it's patterns in your design.

Style:
- Looking for an Elegant, Luxurious, Upmarket feel.
- Black/Matte Black Card, Gold Foil, UV Embossing

Information to Add:

- Logo
- Company Name: Rima Vale Honey
- Name: Martin Holloway
- Title: Creative Director
- Phone: +64 2815 96 417
- Email: martin@rimavalehoney.example.nz
- Website: www.rimavalehoney.example.nz

- Socials: ***For email Signature Only***
- Facebook: https://www.facebook.com/rimavalehoney/
- Instagram: https://www.instagram.com/rimavalehoney/

Target Market(s)

Asia/Europe Luxury, Upmarket

Contact Information for Business Card

- Logo
- Name: Martin Holloway
- Phone: +64 2815 96 417

Font styles to use
Other font styles liked:
• Champagne & Limousines (Attached)

Requirements
Must have
• Business Card & Email Signature Design.

Looking for a Sleek, Luxury, Upmarket Design.

```html
<!DOCTYPE html>
<html lang="en">
<head>
<meta charset="utf-8">
<title>Rima Vale Honey — Email Signature</title>
<link rel="stylesheet" href="https://fonts.googleapis.com/css2?family=Montserrat:wght@400;500;600&display=swap">
<style>
  :root {
    --stage: #1e1e1f;
    --brand-panel: #121212;
    --info-panel: #1b1b1b;
    --gold-light: #f4e690;
    --gold-mid: #d8bf74;
    --gold-deep: #b8914f;
    --text-white: #ffffff;
  }
  * { margin: 0; padding: 0; box-sizing: border-box; }
  html, body {
    width: 1200px; height: 800px; overflow: hidden;
    background: var(--stage);
    font-family: "Montserrat", Arial, sans-serif;
  }
  .signature {
    position: absolute; left: 106px; top: 206px;
    width: 990px; height: 390px;
    display: flex;
    box-shadow: 0 18px 40px rgba(0,0,0,0.55);
  }
  .brand-panel {
    width: 370px; height: 100%;
    background: var(--brand-panel);
    display: flex; align-items: center; justify-content: center;
  }
  .brand-name {
    color: var(--gold-mid);
    font-size: 24px; font-weight: 500;
    letter-spacing: 0.18em; text-transform: uppercase;
    white-space: nowrap;
  }
  .info-panel {
    position: relative; flex: 1; height: 100%;
    background: var(--info-panel);
  }
  .info-panel::before {
    content: ""; position: absolute; left: 0; top: 60px; bottom: 60px; width: 14px;
    background: linear-gradient(to right, rgba(244,230,144,0.35), rgba(244,230,144,0));
    -webkit-mask: linear-gradient(to bottom, transparent, #000 30%, #000 70%, transparent);
    mask: linear-gradient(to bottom, transparent, #000 30%, #000 70%, transparent);
  }
  .person-name {
    position: absolute; left: 51px; top: 68px;
    font-size: 36px; font-weight: 600; letter-spacing: 0.01em; line-height: 1.22;
    text-transform: uppercase; white-space: nowrap;
    background: linear-gradient(90deg, var(--gold-light) 0%, var(--gold-light) 40%, var(--gold-deep) 55%, var(--gold-mid) 100%);
    -webkit-background-clip: text; background-clip: text; color: transparent;
  }
  .person-title {
    position: absolute; left: 50px; top: 109px;
    font-size: 27px; font-weight: 400; line-height: 1.22; color: var(--text-white);
    white-space: nowrap;
  }
  .rule { height: 2px; background: var(--gold-light); }
  .rule-top { position: absolute; left: 51px; right: 2px; top: 160px; }
  .contact-row {
    position: absolute; left: 51px; height: 30px;
    display: flex; align-items: center;
    color: var(--text-white); font-size: 24px; font-weight: 400; white-space: nowrap;
  }
  .contact-row svg { width: 17px; height: 17px; fill: var(--gold-light); flex: none; }
  .contact-row span { position: absolute; left: 29px; }
  .row-phone { top: 180px; }
  .row-email { top: 211px; }
  .row-web { top: 244px; }
  .row-web span { letter-spacing: 0.12em; }
  .social-row {
    position: absolute; left: 51px; right: 0; top: 293px; height: 24px;
    display: flex; align-items: center;
  }
  .social-handle {
    display: flex; align-items: center; gap: 10px; flex: none;
    color: var(--gold-light); font-size: 18px; font-weight: 400;
    letter-spacing: 0.14em; text-transform: uppercase; white-space: nowrap;
  }
  .social-mark { width: 14px; height: 14px; background: var(--gold-light); border-radius: 2px; }
  .rule-social { flex: 1; margin-left: 12px; }
</style>
</head>
<body>
  <main class="signature">
    <section class="brand-panel">
      <div class="brand-name">Rima Vale Honey</div>
    </section>
    <section class="info-panel">
      <h1 class="person-name">Martin Holloway</h1>
      <p class="person-title">Creative Director</p>
      <div class="rule rule-top"></div>

      <div class="contact-row row-phone">
        <svg viewBox="0 0 24 24" aria-hidden="true"><path d="M6.6 10.8a15.1 15.1 0 0 0 6.6 6.6l2.2-2.2c.3-.3.7-.4 1-.2 1.1.4 2.3.6 3.6.6.6 0 1 .4 1 1V20c0 .6-.4 1-1 1A17 17 0 0 1 3 4c0-.6.4-1 1-1h3.5c.6 0 1 .4 1 1 0 1.3.2 2.5.6 3.6.1.3 0 .7-.2 1z"/></svg>
        <span>+64 2815 96 417</span>
      </div>
      <div class="contact-row row-email">
        <svg viewBox="0 0 24 24" aria-hidden="true"><path d="M2 5h20v2l-10 6L2 7z M2 9.3l10 6 10-6V19H2z"/></svg>
        <span>martin@rimavalehoney.example.nz</span>
      </div>
      <div class="contact-row row-web">
        <svg viewBox="0 0 24 24" aria-hidden="true"><circle cx="12" cy="12" r="10"/><path d="M5 8c2 0 3 1 3 3s2 2 2 4-1 3-1 5M14 3c0 2 1 3 3 3s3 2 2 4" stroke="#1b1b1b" stroke-width="1.6" fill="none"/></svg>
        <span>www.rimavalehoney.example.nz</span>
      </div>

      <div class="social-row">
        <div class="social-handle">
          <div class="social-mark"></div>
          <span>/rimavalehoney</span>
        </div>
        <div class="rule rule-social"></div>
      </div>
    </section>
  </main>
</body>
</html>
```